Residential Remodeling Contractor needs updated business card

I need a new design for my business card.
Name of the company is Ridgefell Construction. I need a card that commands presence, strength, integrity. I have been in business for 28 years. I am a Residential Remodeling Contractor that covers all aspects of a residential remodel and build.

```html
<!DOCTYPE html>
<html lang="en">
<head>
<meta charset="utf-8">
<title>Ridgefell Construction – Business Card</title>
<link rel="stylesheet" href="https://fonts.googleapis.com/css2?family=Arimo:wght@400;700&display=swap">
<style>
  :root {
    --stage: #3b3438;
    --card-blue: #1b3f80;
    --card-back-blue: #21407f;
    --emboss-blue: #2c4d8e;
    --ink-white: #ffffff;
    --ink-soft: #dfe6f3;
    --shadow: rgba(0, 0, 0, 0.45);
  }
  * { box-sizing: border-box; margin: 0; padding: 0; }
  html, body {
    width: 1200px; height: 912px; overflow: hidden;
    background: var(--stage);
  }
  .canvas { position: relative; width: 1200px; height: 912px; }

  .card {
    position: absolute;
    width: 620px; height: 354px;
    border-radius: 22px;
    box-shadow: 0 14px 30px var(--shadow);
    overflow: hidden;
  }

  /* Back side */
  .card-back {
    left: 60px; top: 60px;
    background: var(--card-back-blue);
    display: flex; align-items: center; justify-content: center;
  }
  .back-name {
    font-family: "Arimo", sans-serif;
    font-weight: 700;
    color: var(--emboss-blue);
    font-size: 46px;
    line-height: 1.1;
    letter-spacing: 1px;
    text-align: left;
  }
  .back-name span { display: block; }

  /* Front side */
  .card-front {
    left: 520px; top: 498px;
    background: var(--card-blue);
    color: var(--ink-white);
  }
  .company-name {
    position: absolute; left: 250px; top: 48px;
    font-family: "Arimo", sans-serif;
    font-weight: 700;
    font-size: 28px;
    line-height: 1.12;
    letter-spacing: 0.5px;
    color: var(--ink-white);
  }
  .company-name span { display: block; }

  .person {
    position: absolute; left: 20px; top: 196px;
    width: 262px;
    font-family: "Arimo", sans-serif;
    text-align: right;
    white-space: nowrap;
  }
  .person-name { font-weight: 700; font-size: 24px; letter-spacing: 0.5px; }
  .person-title { font-weight: 400; font-size: 14px; margin-top: 4px; }

  .divider {
    position: absolute; left: 300px; top: 178px;
    width: 1px; height: 84px;
    background: var(--ink-soft);
  }

  .contacts {
    position: absolute; left: 320px; top: 172px;
    list-style: none;
    font-family: "Arimo", sans-serif;
    font-size: 13.5px;
    white-space: nowrap;
  }
  .contacts li {
    display: flex; align-items: center; gap: 8px;
    height: 30px;
  }
  .contacts svg { width: 13px; height: 13px; flex: none; fill: var(--ink-white); }

  .address {
    position: absolute; left: 0; right: 0; top: 300px;
    text-align: center;
    font-family: "Arimo", sans-serif;
    font-size: 14px;
    letter-spacing: 0.3px;
  }
</style>
</head>
<body>
  <main class="canvas">
    <section class="card card-back" aria-label="Card back">
      <div class="back-name">
        <span>RIDGEFELL</span>
        <span>CONSTRUCTION</span>
      </div>
    </section>

    <section class="card card-front" aria-label="Card front">
      <div class="company-name">
        <span>RIDGEFELL</span>
        <span>CONSTRUCTION</span>
      </div>

      <div class="person">
        <div class="person-name">MARCO DELGADO</div>
        <div class="person-title">Owner &amp; Manager</div>
      </div>

      <div class="divider"></div>

      <ul class="contacts">
        <li>
          <svg viewBox="0 0 16 16" aria-hidden="true"><path d="M3 1h3l1.5 4-2 1.5a9 9 0 0 0 4 4L11 8.5l4 1.5v3a2 2 0 0 1-2 2A13 13 0 0 1 1 3a2 2 0 0 1 2-2z"/></svg>
          555 014 2287
        </li>
        <li>
          <svg viewBox="0 0 16 16" aria-hidden="true"><path d="M1 3h14v10H1z M2 4l6 5 6-5" fill="none" stroke="#fff" stroke-width="1.5"/></svg>
          info@ridgefellconstruction.com
        </li>
        <li>
          <svg viewBox="0 0 16 16" aria-hidden="true"><circle cx="8" cy="8" r="6.5" fill="none" stroke="#fff" stroke-width="1.5"/><path d="M1.5 8h13M8 1.5c-3 3.5-3 9.5 0 13M8 1.5c3 3.5 3 9.5 0 13" fill="none" stroke="#fff" stroke-width="1.2"/></svg>
          www.ridgefellconstruction.com
        </li>
      </ul>

      <p class="address">P.O. Box 118&nbsp; Street Name Country Name AB, R4K 207</p>
    </section>
  </main>
</body>
</html>
```